Business card design for new eCommerce site focusing on integrity and strong businsess tactics

We need a business card that will stand out and be memorable. Something with color that matches our company logo colors. Think high end version of Pactivo. There are 2 logos provided. The parent company is called Amber Ledge Partners and we are presenting a new and very exciting eCommerce site called BrightHarborTrade.example.

Target Market(s)

Our target markets are in the Activities, Food and Beverage, Health and Beauty

Industry/Entity Type

Marketing

Contact Information for Business Card

We have 4 members that need cards...I will provide all info to the winner of the design contest
Business Address is
4870 West 63rd Avenue, Suite C207
Phoenix AZ 85731

Font styles to use
Serif
Sans Serif

Colors

Designer to choose colors to be used in the design.

Requirements
Must have
• The card must be memorable...should be unique in design but must exude integrity and be playful .
• I have provided several colors or our parent company...please feel free to use which ever
Nice to have
• I will leave this up to you. Feel free to use other images of your choosing that wraps around our client.....Activities, Dining, Health, Beauty
Should not have
• just dont be boring

```html
<!DOCTYPE html>
<html lang="en">
<head>
<meta charset="utf-8">
<title>BrightHarborTrade.example – Business Card</title>
<link rel="stylesheet" href="https://fonts.googleapis.com/css2?family=Jost:wght@400;500;600&display=swap">
<style>
  :root {
    --backdrop: #2a2a2a;
    --blue-light: #3fbcd8;
    --blue-deep: #2a78b0;
    --blue-stripe: #2c7cb6;
    --green: #8dc63f;
    --green-light: #b8de52;
    --green-deep: #76bf32;
    --paper: #f3f3f3;
    --white: #ffffff;
    --grey-text: #5a5a5a;
  }
  * { margin: 0; padding: 0; box-sizing: border-box; }
  html, body { width: 1200px; height: 960px; overflow: hidden; }
  body {
    background: var(--backdrop);
    font-family: "Jost", "Futura", sans-serif;
    position: relative;
  }
  .card {
    position: absolute;
    width: 600px;
    height: 342px;
    border-radius: 18px;
    overflow: hidden;
  }
  .card-front { left: 302px; top: 131px; background: var(--paper); }
  .card-back {
    left: 299px; top: 490px;
    background: linear-gradient(135deg, var(--green-light) 0%, var(--green-deep) 45%, var(--green-deep) 100%);
  }
  .front-art { position: absolute; inset: 0; }
  .contact-block {
    position: absolute;
    left: 28px;
    top: 73px;
    color: var(--white);
  }
  .person-name {
    color: var(--green);
    font-size: 23px;
    font-weight: 600;
    letter-spacing: 0;
    line-height: 1;
  }
  .person-title {
    font-size: 14px;
    margin-top: 6px;
    line-height: 1;
  }
  .address {
    font-size: 14px;
    line-height: 18px;
    margin-top: 14px;
  }
  .contact-list {
    list-style: none;
    margin-top: 14px;
    font-size: 14px;
    line-height: 19.4px;
  }
  .contact-list li { display: flex; align-items: center; }
  .contact-icon { width: 12px; height: 12px; margin-right: 9px; flex: none; }
  .front-brand {
    position: absolute;
    right: 22px;
    top: 150px;
    text-align: right;
  }
  .brand-name {
    color: var(--blue-stripe);
    font-size: 19px;
    font-weight: 500;
    line-height: 1;
  }
  .brand-tagline {
    color: var(--grey-text);
    font-size: 12px;
    letter-spacing: 1.6px;
    margin-top: 6px;
  }
  .back-brand {
    position: absolute;
    left: 0; right: 0;
    top: 134px;
    text-align: center;
    color: var(--white);
  }
  .back-brand .brand-name {
    color: var(--white);
    font-size: 34px;
    font-weight: 500;
  }
  .back-brand .brand-tagline {
    color: var(--white);
    font-size: 18px;
    letter-spacing: 2.4px;
    margin-top: 10px;
  }
  .motto {
    position: absolute;
    left: 120px; right: 120px;
    top: 279px;
    display: flex;
    align-items: center;
    gap: 6px;
    color: var(--white);
    font-size: 14px;
    font-weight: 600;
    letter-spacing: 1px;
    white-space: nowrap;
  }
  .motto-rule { flex: 1; height: 1.5px; }
  .motto-rule.left { background: linear-gradient(90deg, transparent, var(--white)); }
  .motto-rule.right { background: linear-gradient(90deg, var(--white), transparent); }
</style>
</head>
<body>

<section class="card card-front" aria-label="Business card front">
  <svg class="front-art" viewBox="0 0 600 342" width="600" height="342" aria-hidden="true">
    <defs>
      <linearGradient id="panelBlue" x1="0" y1="0" x2="1" y2="1">
        <stop offset="0" stop-color="#3fbcd8"/>
        <stop offset="0.45" stop-color="#2a82b8"/>
        <stop offset="1" stop-color="#2a78b0"/>
      </linearGradient>
    </defs>
    <path d="M0,0 H308 C248,55 232,140 282,225 C322,292 322,318 305,342 H0 Z" fill="url(#panelBlue)"/>
    <path d="M300,0 C244,55 232,140 282,225 C322,292 322,318 305,342" fill="none" stroke="#ffffff" stroke-width="10"/>
    <path d="M312,0 C258,50 246,140 296,228 C334,296 332,320 314,342" fill="none" stroke="#2c7cb6" stroke-width="6"/>
    <path d="M308,4 C276,30 262,70 266,110" fill="none" stroke="#8dc63f" stroke-width="5" stroke-linecap="round"/>
    <path d="M278,190 C320,250 326,300 300,338" fill="none" stroke="#8dc63f" stroke-width="5" stroke-linecap="round"/>
  </svg>

  <div class="contact-block">
    <h1 class="person-name">DANA WHITFIELD</h1>
    <p class="person-title">PRESIDENT</p>
    <p class="address">4870 West 63rd Avenue<br>Suite C207<br>Phoenix AZ 85731</p>
    <ul class="contact-list">
      <li>
        <svg class="contact-icon" viewBox="0 0 12 12" aria-label="Phone"><path d="M2.5 1 L4.5 1 L5.3 3.6 L4 4.6 C4.7 6 6 7.3 7.4 8 L8.4 6.7 L11 7.5 L11 9.5 C11 10.3 10.3 11 9.5 11 C5 11 1 7 1 2.5 C1 1.7 1.7 1 2.5 1 Z" fill="#8dc63f"/></svg>
        602-555-0174
      </li>
      <li>
        <svg class="contact-icon" viewBox="0 0 12 12" aria-label="Mobile"><rect x="3" y="0.5" width="6" height="11" rx="1.2" fill="none" stroke="#8dc63f" stroke-width="1.3"/><circle cx="6" cy="9.6" r="0.7" fill="#8dc63f"/></svg>
        602-555-0139
      </li>
      <li>
        <svg class="contact-icon" viewBox="0 0 12 12" aria-label="Email"><rect x="0.5" y="2.5" width="11" height="7.5" fill="#8dc63f"/><path d="M0.5 2.5 L6 6.8 L11.5 2.5" fill="none" stroke="#2a80b6" stroke-width="1"/></svg>
        Dana@BrightHarborTrade.example
      </li>
      <li>
        <svg class="contact-icon" viewBox="0 0 12 12" aria-label="Website"><circle cx="6" cy="6" r="5.3" fill="#8dc63f"/><path d="M1 6 H11 M6 0.8 C3.5 3.5 3.5 8.5 6 11.2 M6 0.8 C8.5 3.5 8.5 8.5 6 11.2" fill="none" stroke="#2a80b6" stroke-width="0.8"/></svg>
        www.BrightHarborTrade.example
      </li>
    </ul>
  </div>

  <div class="front-brand">
    <p class="brand-name">BrightHarborTrade.example</p>
    <p class="brand-tagline">Outings-Eating-Wellness-Styling</p>
  </div>
</section>

<section class="card card-back" aria-label="Business card back">
  <div class="back-brand">
    <p class="brand-name">BrightHarborTrade.example</p>
    <p class="brand-tagline">Outings-Eating-Wellness-Styling</p>
  </div>
  <div class="motto">
    <span class="motto-rule left"></span>
    <span>ALWAYS ON YOUR SIDE</span>
    <span class="motto-rule right"></span>
  </div>
</section>

</body>
</html>
```